Business Card for a Jewellery Brand

Business card for an upscale jewellery brand. Attached is the brand logo and icon and color board. I am looking for two card versions: one for the founder and one is generic. The card should be elegant and convey upscale and premium feel. I am open to both square and rectangle card shapes.

Industry/Entity Type

Jewelry

Contact Information for Business Card

Two cards: (1) Sunela Parvaniya (Founder) (2) General
(1) Sunela Parvaniya card should have Name: Sunela Parvaniya, Title: Founder Email id: sunela@quiremo.com.au. Phone no: +61452913307
(2) Generic card should have Email id: info@quiremo.com.au. Phone no: +61436207518

Requirements
Must have
• Workmark
• ICON
• Phone no
• Email ID
• ABN: 58219740312 (Note: ABN is Business number in Australia)
• Website: www.quiremo.com.au
• Instagram: quiremo_jewellery
• Facebook: @quiremojewellery
Nice to have
• Tagline

```html
<!DOCTYPE html>
<html lang="en">
<head>
<meta charset="utf-8">
<title>Quiremo Business Cards</title>
<link href="https://fonts.googleapis.com/css2?family=Roboto:wght@400&family=Saira+Semi+Condensed:wght@600&display=swap" rel="stylesheet">
<style>
  :root {
    --backdrop: #e2e2e2;
    --card: #f3ddd7;
    --rose: #d4828b;
    --ink: #5a5a5a;
    --icon: #d58a92;
  }
  html, body {
    margin: 0;
    width: 1200px;
    height: 960px;
    overflow: hidden;
    background: var(--backdrop);
  }
  .stage {
    position: relative;
    width: 1200px;
    height: 960px;
  }
  .card {
    position: absolute;
    width: 600px;
    height: 341px;
    background: var(--card);
    box-shadow: 1px 2px 3px rgba(0,0,0,0.35);
  }
  .card--front { left: 302px; top: 130px; }
  .card--back  { left: 300px; top: 490px; }

  .person {
    position: absolute;
    left: 60px;
    top: 86px;
  }
  .person__name {
    margin: 0;
    font-family: "Saira Semi Condensed", sans-serif;
    font-weight: 600;
    font-size: 21px;
    line-height: 1;
    color: var(--rose);
    text-transform: uppercase;
  }
  .person__title {
    margin: 6px 0 0;
    font-family: "Roboto", sans-serif;
    font-size: 15.5px;
    color: var(--ink);
  }
  .contacts {
    list-style: none;
    margin: 16px 0 0;
    padding: 0;
    font-family: "Roboto", sans-serif;
    font-size: 14px;
    color: var(--ink);
  }
  .contacts li {
    display: flex;
    align-items: center;
    height: 18px;
  }
  .contacts svg {
    width: 12px;
    height: 12px;
    margin-right: 9px;
    flex: none;
  }
  .abn {
    margin: 15px 0 0;
    font-family: "Roboto", sans-serif;
    font-size: 15px;
    color: var(--rose);
  }

  .brand {
    position: absolute;
    left: 363px;
    top: 50%;
    transform: translate(-50%, -50%);
    display: flex;
    flex-direction: column;
    align-items: center;
    margin-top: 20px;
  }
  .brand__mark {
    width: 76px;
    height: 76px;
    border: 3px solid var(--rose);
    border-radius: 50%;
    margin-bottom: 30px;
  }
  .brand__name {
    font-family: "Roboto", sans-serif;
    font-weight: 400;
    font-size: 50px;
    line-height: 1;
    letter-spacing: 0.18em;
    margin-right: -0.18em;
    color: var(--rose);
  }
</style>
</head>
<body>
<main class="stage">

  <section class="card card--front" aria-label="Founder card, front">
    <div class="person">
      <h1 class="person__name">Sunela Parvaniya</h1>
      <p class="person__title">Founder</p>
      <ul class="contacts">
        <li>
          <svg viewBox="0 0 12 12" aria-hidden="true"><rect x="2.5" y="0.5" width="7" height="11" rx="1" fill="none" stroke="var(--icon)" stroke-width="1.4"/><rect x="5" y="9" width="2" height="1" fill="var(--icon)"/></svg>
          +61452913307
        </li>
        <li>
          <svg viewBox="0 0 12 12" aria-hidden="true"><rect x="0.5" y="2" width="11" height="8" fill="var(--icon)"/><path d="M0.5 2.5 L6 6.5 L11.5 2.5" fill="none" stroke="var(--card)" stroke-width="1"/></svg>
          sunela@quiremo.com.au
        </li>
        <li>
          <svg viewBox="0 0 12 12" aria-hidden="true"><circle cx="6" cy="6" r="5.5" fill="var(--icon)"/><path d="M1 6 H11 M6 0.5 V11.5" stroke="var(--card)" stroke-width="0.8"/><ellipse cx="6" cy="6" rx="2.3" ry="5.5" fill="none" stroke="var(--card)" stroke-width="0.8"/></svg>
          www.quiremo.com.au
        </li>
        <li>
          <svg viewBox="0 0 12 12" aria-hidden="true"><rect x="1" y="1" width="10" height="10" fill="var(--icon)"/></svg>
          quiremo_jewellery
        </li>
        <li>
          <svg viewBox="0 0 12 12" aria-hidden="true"><rect x="1" y="1" width="10" height="10" fill="var(--icon)"/></svg>
          @quiremojewellery
        </li>
      </ul>
      <p class="abn">ABN: 58219740312</p>
    </div>
  </section>

  <section class="card card--back" aria-label="Card back with brand name">
    <div class="brand">
      <div class="brand__mark" aria-hidden="true"></div>
      <div class="brand__name">QUIREMO</div>
    </div>
  </section>

</main>
</body>
</html>
```